A modern and fresh looking church website

Elmridge is looking for a new site design for their church. The church is a part of a group of the ‘Covenant Fellowship’ Australia and needs to kind of tie into their branding within reason.
This means, we would need to use the logo colours (Blue, Gold, Red) throughout the website and the design needs to be fresh, modern, clean, and mobile-friendly. The front page must have the following as features:
• Sermons (Podcasts and Videos)
• Events
• Venue Hire (Weddings)
The website will be mainly information-based and will have a few forms. From our recent engagement with the church, I did draft up a mock-up design for them and even it looks better than their current site, it’s not giving a ‘stand out impression’ and has that out of date look.
The inner pages will be based off the front-page design so we will take care of that, we are just looking for a front-page design that is unique and has the wow factor.
The website will be coded by our in-house development team and will be coded in a WordPress format using Elementor pro.
We are looking for a couple of designers to design 1-3 mock-ups by taking our current draft and putting their spin to it.
Updates
Hi,
Due to Christmas and the client was on leave, the design selection has been delayed. It was not ideal as I knew this would happen.
I made contact with the client and just been told that the client is leaving the church and a handover is happening for the new staff member. The new staff member will present all designs to the board for selection. This is due to be completed by the first week of February 2021.
We thanks for your patients as this was not expected and we seeing if we can hurry this process up.

```html
<!DOCTYPE html>
<html lang="en">
<head>
<meta charset="utf-8">
<title>Elmridge – Covenant Fellowship</title>
<link href="https://fonts.googleapis.com/css2?family=Lora:wght@700&family=Montserrat:wght@600;700;800&family=Rubik:wght@300;400;500&family=Tinos:wght@400;700&display=swap" rel="stylesheet">
<style>
:root{
  --blue:#1a4c9c;
  --blue-dark:#0f2e5e;
  --navy:#132f63;
  --red:#e3262b;
  --gold:#f6a44f;
  --ink:#1b1b1b;
  --grey:#555;
}
*{box-sizing:border-box;margin:0;padding:0}
html,body{width:1200px;height:2983px;overflow:hidden;background:#fff}
body{font-family:"Tinos",serif;color:var(--ink)}
.page{position:relative;width:1200px;height:2983px;overflow:hidden}
.abs{position:absolute}

/* top bar */
.topbar{left:0;top:0;width:1200px;height:35px;background:var(--blue);color:#fff;font-size:13px}
.topbar .addr{left:96px;top:0;line-height:35px;display:flex;align-items:center;gap:10px}
.topbar .social{right:92px;top:0;display:flex;height:35px}
.topbar .social span{width:50px;height:35px;border-left:1px solid rgba(255,255,255,.3);display:flex;align-items:center;justify-content:center}
.topbar .social i{width:14px;height:14px;border-radius:50%;background:#fff;display:block}

/* header */
.brand{left:94px;top:60px;display:flex;align-items:center;gap:14px}
.brand .dot{width:52px;height:52px;border-radius:50%;background:var(--blue)}
.brand .name{font-family:"Montserrat",sans-serif;font-weight:700;color:var(--blue);font-size:30px;line-height:1}
.brand .sub{font-family:"Montserrat",sans-serif;font-weight:700;color:var(--blue);font-size:12px;letter-spacing:.5px;margin-top:6px}
.service{left:968px;top:56px;font-size:12.5px;color:var(--gold);line-height:16px}
.service b{display:block;font-family:"Montserrat",sans-serif;color:var(--blue);font-size:13px;text-decoration:underline;margin-bottom:4px}

/* nav */
.ribbon{left:86px;top:162px}
.nav{left:127px;top:162px;width:944px;height:52px;background:var(--blue);display:flex;padding-left:43px}
.nav a{font-family:"Tinos",serif;font-weight:700;font-size:14.5px;color:#fff;text-decoration:none;line-height:52px;padding:0 24px;text-transform:uppercase}
.nav a.on{background:var(--red)}

/* hero */
.hero{left:0;top:197px;width:1200px;height:557px;background:linear-gradient(180deg,#eeedf0,#e3e2e6)}
.hero h1{left:90px;top:116px;font-family:"Lora",serif;font-weight:700;font-size:63px;line-height:62px;color:#111}
.hero h1 em{font-style:normal;color:var(--red)}
.hero .motto{left:102px;top:256px;width:174px;border-top:1px solid #aaa;border-bottom:1px solid #aaa;padding:8px 2px;font-family:"Rubik",sans-serif;font-weight:300;font-size:17px;letter-spacing:.3px;color:#333}
.hero .btn{left:102px;top:328px;width:171px;height:58px;background:var(--red);border-radius:6px;color:#fff;font-family:"Montserrat",sans-serif;font-weight:700;font-size:12px;display:flex;align-items:center;justify-content:center;box-shadow:0 4px 0 #a91218}
.hero .tagline{left:118px;top:430px;width:700px;height:50px;background:linear-gradient(90deg,rgba(232,130,130,.35),rgba(232,130,130,.08));border-radius:25px}
.hero .dome{left:787px;top:81px;width:301px;height:476px;background:linear-gradient(180deg,#c9c7cb 0%,#9aa59d 55%,#b9b5b2 100%);border-radius:150px 150px 0 0}

/* covid */
.alert{left:154px;top:780px;width:892px;height:51px;border-radius:6px;background:linear-gradient(180deg,#2a66b5,#153e80);color:#fff;display:flex;align-items:center}
.alert .ic{width:52px;display:flex;justify-content:center}
.alert h4{font-family:"Rubik",sans-serif;font-weight:500;font-size:13px}
.alert p{font-size:10.5px;margin-top:4px}

/* about */
.about{left:0;top:860px;width:1200px;height:623px;background:linear-gradient(180deg,#fff,#f6f7f9)}
.about h2{left:0;top:20px;width:1200px;text-align:center;font-family:"Montserrat",sans-serif;font-weight:800;font-size:21px}
.about .rule{left:489px;top:56px;width:222px;height:1px;background:#999}
.about .copy{left:220px;top:90px;width:760px;text-align:center;font-size:14.5px;line-height:21.5px;color:#333}
.about .copy p{margin-bottom:21px}
.about .copy b{color:var(--red)}
.about .divider{left:185px;top:356px;width:830px;height:1px;background:#f2c4c4}
.feature{top:392px;width:200px;text-align:center}
.feature .ring{width:112px;height:112px;border-radius:50%;border:1.5px dashed var(--blue);margin:0 auto;display:flex;align-items:center;justify-content:center}
.feature h3{font-family:"Montserrat",sans-serif;font-weight:700;font-size:16px;color:#333;margin-top:20px}
.feature p{font-size:11px;line-height:17px;color:#555;margin-top:10px}

/* services */
.services{left:0;top:1483px;width:1200px;height:557px;background:linear-gradient(180deg,#2b67b6,#1d4c95 70%,#24508f)}
.services h2{left:0;top:58px;width:1200px;text-align:center;color:#fff;font-family:"Montserrat",sans-serif;font-weight:800;font-size:21px}
.card{top:152px;width:351px;height:287px;background:#fff;padding:7px}
.card .photo{width:100%;height:223px}
.card .label{height:50px;background:var(--gold);color:var(--blue);font-family:"Montserrat",sans-serif;font-weight:700;font-size:14.5px;display:flex;align-items:center;justify-content:center}

/* map + contact */
.map{left:0;top:2040px;width:1200px;height:557px;background:linear-gradient(135deg,#ebedee 0%,#e4e8ea 60%,#aed6f3 78%,#9fcdf0 100%)}
.contact{left:279px;top:2154px;width:642px;height:341px;background:rgba(246,164,79,.93)}
.contact h2{left:0;top:38px;width:642px;text-align:center;font-family:"Montserrat",sans-serif;font-weight:800;font-size:20px;color:#111}
.citem{display:flex;align-items:center;gap:17px;font-size:17px;line-height:20px;color:#222}
.citem .ci{width:40px;height:40px;border-radius:50%;border:1.5px dashed var(--blue);display:flex;align-items:center;justify-content:center;flex:none}

/* footer */
.footer{left:0;top:2597px;width:1200px;height:386px;background:var(--navy);color:#fff}
.footer h4{font-family:"Montserrat",sans-serif;font-weight:700;font-size:16px;position:absolute;top:42px}
.footer h4::after{content:"";display:block;width:80px;height:1px;background:rgba(255,255,255,.6);margin-top:10px}
.fbrand{left:146px;top:36px;background:#fff;padding:6px 8px;display:flex;align-items:center;gap:8px}
.fbrand i{width:26px;height:26px;border-radius:50%;background:var(--blue)}
.fbrand span{font-family:"Montserrat",sans-serif;font-weight:700;color:var(--blue);font-size:17px}
.ftag{left:146px;top:92px;width:196px;height:28px;border-radius:14px;background:rgba(255,255,255,.12)}
.fabout{left:146px;top:136px;width:196px;font-size:11px;line-height:17px}
.flinks{left:359px;top:106px;font-size:11px;line-height:26px;list-style:none}
.art{left:535px;display:flex;gap:14px;width:300px}
.art .th{width:52px;height:50px;background:linear-gradient(135deg,#3d7ed6,#e7eefa);flex:none}
.art p{font-family:"Rubik",sans-serif;font-weight:300;font-size:10px;line-height:15px}
.art b{display:block;font-family:"Rubik",sans-serif;font-weight:500;font-size:12px;margin-top:4px}
.fc{left:888px;display:flex;gap:16px;font-size:10.5px;line-height:15px;align-items:flex-start}
.fc svg{flex:none}
.copyright{left:0;top:344px;width:1200px;border-top:1px solid rgba(255,255,255,.2);text-align:center;font-family:"Rubik",sans-serif;font-weight:300;font-size:12px;padding-top:14px}
</style>
</head>
<body>
<div class="page">

  <div class="abs topbar">
    <div class="abs addr">
      <svg width="11" height="15" viewBox="0 0 11 15"><path d="M5.5 0A5.5 5.5 0 0 0 0 5.5C0 9.5 5.5 15 5.5 15S11 9.5 11 5.5A5.5 5.5 0 0 0 5.5 0zm0 7.7a2.2 2.2 0 1 1 0-4.4 2.2 2.2 0 0 1 0 4.4z" fill="#fff"/></svg>
      24 Harrow Lane, Northfield, WA 6000
    </div>
    <div class="abs social"><span><i></i></span><span><i></i></span><span><i></i></span></div>
  </div>

  <div class="abs brand">
    <div class="dot"></div>
    <div>
      <div class="name">ELMRIDGE</div>
      <div class="sub">COVENANT FELLOWSHIP</div>
    </div>
  </div>
  <div class="abs service"><b>WEKEND SERVICE</b>Saturday 6pm<br>Suday 8:30am &amp; 10:20am</div>

  <svg class="abs ribbon" width="1028" height="64" viewBox="0 0 1028 64">
    <polygon points="0,12 41,12 41,64 66,64 66,57 20,57 30,34" fill="#1a4c9c"/>
    <polygon points="1028,12 987,12 987,64 962,64 962,57 1008,57 998,34" fill="#1a4c9c"/>
    <polygon points="41,52 66,57 41,64" fill="#0f2e5e"/>
    <polygon points="987,52 962,57 987,64" fill="#0f2e5e"/>
  </svg>
  <nav class="abs nav">
    <a class="on" href="#">Home</a><a href="#">Sermons</a><a href="#">About Us ⌄</a><a href="#">Church</a><a href="#">Life News</a><a href="#">Weddings</a><a href="#">Contact Us</a>
  </nav>

  <section class="abs hero">
    <h1 class="abs">WE Believe that<br>GOD <em>loves Us</em></h1>
    <div class="abs motto">LOVE. GROW. SERVE</div>
    <div class="abs btn">GET IN TOUCH</div>
    <div class="abs tagline" role="img" aria-label="Decorative leaf and flowing line with a hand-lettered welcome phrase"></div>
    <div class="abs dome" role="img" aria-label="Photo of a snow-dusted green church dome topped with a cross"></div>
  </section>

  <div class="abs alert">
    <div class="ic"><svg width="20" height="18" viewBox="0 0 20 18"><path d="M10 1 19 17H1z" fill="none" stroke="#fff" stroke-width="1.6"/><path d="M10 7v5M10 14v1" stroke="#fff" stroke-width="1.6"/></svg></div>
    <div><h4>Elmridge’s response to COVID-19</h4><p>Lorem ipsum dolor sit amet, consectetur adipiscing elit, sed do eiusmod tempor incididunt ut labore et dolore magna aliqua.</p></div>
  </div>

  <section class="abs about">
    <h2 class="abs">About Growth Hack</h2>
    <div class="abs rule"></div>
    <div class="abs copy">
      <p>Lorem ipsum dolor sit amet, consectetur adipisicing elit, sed do eiusmod tempor incididunt ut labore et dolore magna aliqua. Ut enim ad minim veniam, quis nostrud exercitation ullamco laboris nisi ut aliquip ex ea commodo consequat. Duis aute irure dolor in reprehenderit in voluptate velit esse <b>cillum dolore</b> eu fugiat nulla pariatur.</p>
      <p>Excepteur sint occaecat cupidatat non proident, sunt in culpa qui officia deserunt mollit anim id est laborum. Sed ut perspiciatis unde omnis iste natus error sit <b>voluptatem accusantium</b> doloremque laudantium, totam rem aperiam,</p>
      <p>Nemo enim ipsam voluptatem quia voluptas sit aspernatur aut odit aut fugit, sed quia consequuntur magni dolores eos qui ratione <b>voluptatem sequi</b> nesciunt. Neque porro quisquam est, qui dolorem ipsum quia dolor sit amet, consectetur, adipisci velit, sed quia non numquam eius modi <b>tempora incidunt</b> ut labore et dolore magnam aliquam quaerat voluptatem.</p>
    </div>
    <div class="abs divider"></div>

    <div class="abs feature" style="left:274px">
      <div class="ring"><svg width="52" height="52" viewBox="0 0 52 52"><circle cx="17" cy="10" r="6" fill="none" stroke="#1a4c9c" stroke-width="3"/><circle cx="35" cy="10" r="6" fill="none" stroke="#1a4c9c" stroke-width="3"/><path d="M8 50V26q0-8 9-8t9 8v24zM28 50l4-24q1-8 5-8t5 8l4 24z" fill="#1a4c9c"/></svg></div>
      <h3>LOREM IPSUM</h3>
      <p>Lorem ipsum dolor sit<br>amet,ultrices gravida.<br>Risus com</p>
    </div>
    <div class="abs feature" style="left:500px">
      <div class="ring"><svg width="52" height="52" viewBox="0 0 52 52"><rect x="4" y="8" width="44" height="40" rx="3" fill="#1a4c9c"/><rect x="13" y="3" width="4" height="9" fill="#1a4c9c"/><rect x="35" y="3" width="4" height="9" fill="#1a4c9c"/><g fill="#fff"><rect x="11" y="22" width="6" height="5"/><rect x="20" y="22" width="6" height="5"/><rect x="29" y="22" width="6" height="5"/><rect x="38" y="22" width="4" height="5"/><rect x="11" y="31" width="6" height="5"/><rect x="20" y="31" width="6" height="5"/><rect x="29" y="31" width="6" height="5"/><rect x="38" y="31" width="4" height="5"/></g></svg></div>
      <h3>LOREM IPSUM</h3>
      <p>Lorem ipsum dolor sit<br>amet,ultrices gravida.<br>Risus com</p>
    </div>
    <div class="abs feature" style="left:726px">
      <div class="ring"><svg width="52" height="52" viewBox="0 0 52 52"><circle cx="17" cy="10" r="6" fill="none" stroke="#1a4c9c" stroke-width="3"/><circle cx="35" cy="10" r="6" fill="none" stroke="#1a4c9c" stroke-width="3"/><path d="M8 50V26q0-8 9-8t9 8v24zM28 50l4-24q1-8 5-8t5 8l4 24z" fill="#1a4c9c"/></svg></div>
      <h3>LOREM IPSUM</h3>
      <p>Lorem ipsum dolor sit<br>amet,ultrices gravida.<br>Risus com</p>
    </div>
  </section>

  <section class="abs services">
    <h2 class="abs">Solution for your business</h2>
    <div class="abs card" style="left:56px">
      <div class="photo" role="img" aria-label="Photo of a speaker presenting to a seated audience" style="background:linear-gradient(135deg,#4f88c6,#6a5148 60%,#2e2a2c)"></div>
      <div class="label">ORGANIZED EVENTS</div>
    </div>
    <div class="abs card" style="left:424px">
      <div class="photo" role="img" aria-label="Photo of a couple's hands exchanging a wedding ring" style="background:linear-gradient(135deg,#8a5a4a,#d9a58a 50%,#2b3140)"></div>
      <div class="label">WEDDINGS</div>
    </div>
    <div class="abs card" style="left:792px">
      <div class="photo" role="img" aria-label="Photo of a studio microphone above a desk for podcasts" style="background:linear-gradient(135deg,#d7d9dc,#7d8086 55%,#2a2b2f)"></div>
      <div class="label">RECENT PODDCASTS &amp; VIDEOS</div>
    </div>
  </section>

  <div class="abs map" role="img" aria-label="Street map of the area around the church"></div>
  <section class="abs contact">
    <h2 class="abs">CONTACT US</h2>
    <div class="abs citem" style="left:52px;top:112px">
      <div class="ci"><svg width="20" height="20" viewBox="0 0 20 20"><path d="M4 2l4 3-2 3q2 4 6 6l3-2 3 4-3 3Q7 18 1 5z" fill="#1a4c9c"/></svg></div>
      08 5550 1234
    </div>
    <div class="abs citem" style="left:358px;top:110px">
      <div class="ci"><svg width="20" height="20" viewBox="0 0 20 20"><circle cx="10" cy="10" r="8" fill="none" stroke="#1a4c9c" stroke-width="2"/><path d="M2 10h16M10 2q-5 8 0 16M10 2q5 8 0 16" fill="none" stroke="#1a4c9c" stroke-width="1.5"/></svg></div>
      24 Harrow Lane<br>Northfield, WA 6000
    </div>
    <div class="abs citem" style="left:52px;top:188px">
      <div class="ci"><svg width="20" height="14" viewBox="0 0 20 14"><rect width="20" height="14" rx="2" fill="#1a4c9c"/><path d="M1 1l9 7 9-7" fill="none" stroke="#fff" stroke-width="1.5"/></svg></div>
      hello@elmridgechurch.org
    </div>
    <div class="abs citem" style="left:358px;top:188px">
      <div class="ci"><svg width="20" height="22" viewBox="0 0 20 22"><circle cx="10" cy="13" r="8" fill="none" stroke="#1a4c9c" stroke-width="2.2"/><path d="M10 13V8M7 2h6" stroke="#1a4c9c" stroke-width="2.2"/></svg></div>
      Tue,Th&amp; Fri 9.00-4pm
    </div>
  </section>

  <footer class="abs footer">
    <div class="abs fbrand"><i></i><span>ELMRIDGE</span></div>
    <div class="abs ftag" role="img" aria-label="Hand-lettered welcome phrase"></div>
    <p class="abs fabout">Lorem ipsum dolor sit amet, consectetur adipisicing elit, sed do eiusmod tempor incididunt ut labore et dolore magna aliqua. Ut enim ad minim veniam, quis nostrud.</p>

    <h4 style="left:359px">Quick Links</h4>
    <ul class="abs flinks"><li>Home</li><li>Sernons</li><li>About Us</li><li>Contact Us</li><li>News</li><li>Weddings</li><li>Sitemap</li></ul>

    <h4 style="left:535px">Latest Articles</h4>
    <div class="abs art" style="top:108px"><div class="th" role="img" aria-label="Article thumbnail"></div><p>Lorem ipsum dolor sit amet, conse cterud , cons ectetur, adipis ci velit, sed .<b>1 Dec, 2020</b></p></div>
    <div class="abs art" style="top:185px"><div class="th" role="img" aria-label="Article thumbnail"></div><p>Lorem ipsum dolor sit amet, conse cterud , cons ectetur, adipis ci velit, sed .<b>1 Dec, 2020</b></p></div>
    <div class="abs art" style="top:266px"><div class="th" role="img" aria-label="Article thumbnail"></div><p>Lorem ipsum dolor sit amet, conse cterud , cons ectetur, adipis ci velit, sed .<b>1 Dec, 2020</b></p></div>

    <h4 style="left:892px">Let’s Connect</h4>
    <div class="abs fc" style="top:112px"><svg width="20" height="20" viewBox="0 0 20 20"><path d="M4 2l4 3-2 3q2 4 6 6l3-2 3 4-3 3Q7 18 1 5z" fill="#f6a44f"/></svg><span>08 5550 1234</span></div>
    <div class="abs fc" style="top:144px"><svg width="20" height="20" viewBox="0 0 11 15"><path d="M5.5 0A5.5 5.5 0 0 0 0 5.5C0 9.5 5.5 15 5.5 15S11 9.5 11 5.5A5.5 5.5 0 0 0 5.5 0zm0 7.7a2.2 2.2 0 1 1 0-4.4 2.2 2.2 0 0 1 0 4.4z" fill="#f6a44f"/></svg><span>24 Harrow Lane<br>Northfield, WA 6000</span></div>
    <div class="abs fc" style="top:192px"><svg width="20" height="18" viewBox="0 0 20 18"><path d="M0 9 20 0 14 18 9 11z" fill="#f6a44f"/></svg><span>office@elmridgechurch.org</span></div>

    <div class="abs copyright">© 2020 Elmridge Church &nbsp;LLC.</div>
  </footer>
</div>
</body>
</html>
```